Accountability Project Graphics

I want to create 10 social media graphics (new Instagram size 4:5 (1080 x 1350 pixels) focusing on our Quilvo Accountability App, using any of the 3 pictures attached. Use the attached pics only, NO RANDOM STOCK PHOTOGRAPHY. For the color scheme, use the landing page colors/fonts (attached).
You can add any of the 3 photos attached but I mainly need BOLD text that includes these headlines and sub-headlines on them.
Please NOTE for all the headlines below, also add this sub-headline on each graphic:
Stay Consistent with RT in Your Pocket!
Here are the headlines:
• Stop Starting Over Every Monday
• You don't need more willpower. You need more support
• Built for women who are tired of doing this alone
• When Motivation Fades, RT Checks In
• The Support System You've Been Missing
• Support When Motivation Disappears
• What if RT Checked in Every Day?
• The Missing Piece Isn't Another Diet
• Eat the food you love. Stay accountable every day.
• One Bad Meal Doesn't Mean You Failed
women over 40 trying to lose weight

```html
<!DOCTYPE html>
<html lang="en">
<head>
<meta charset="utf-8">
<title>Quilvo Accountability App – Social Graphics</title>
<link rel="stylesheet" href="https://fonts.googleapis.com/css2?family=Playfair+Display:ital,wght@0,700;0,800;1,700;1,800&family=Poppins:wght@600;700&display=swap">
<style>
:root{
  --backdrop:#e0527f;
  --pink:#e4527e;
  --plum:#2e1e3f;
  --white:#ffffff;
}
*{margin:0;padding:0;box-sizing:border-box}
html,body{width:1200px;height:2957px;overflow:hidden;background:var(--backdrop)}
.board{position:relative;width:1200px;height:2957px}
.post{position:absolute;width:431px;height:539px;overflow:hidden;background:var(--white)}
.post-art{position:absolute;left:0;top:0;width:375px;height:469px;transform:scale(1.1493);transform-origin:0 0}
.shapes{position:absolute;inset:0;width:375px;height:469px}
.plum{fill:var(--plum);stroke:var(--plum)}
.pink{fill:var(--pink);stroke:var(--pink)}
.panel{stroke-linejoin:round;stroke-width:40}
.photo{fill:url(#photoTone);stroke:url(#photoTone);stroke-linejoin:round;stroke-width:40}
.headline{position:absolute;font-family:"Playfair Display",Georgia,serif;font-weight:800;color:var(--white);font-size:31px;line-height:1.17}
.headline em{font-style:italic}
.headline .accent{color:var(--pink)}
.tagline{position:absolute;font-family:"Poppins",Arial,sans-serif;font-weight:700;color:var(--white);font-size:16px;line-height:1.3}
.tagline .accent{color:var(--pink)}
.center{text-align:center;left:0;width:375px}
.col-l{left:158px}.col-r{left:611px}
.row-1{top:86px}.row-2{top:649px}.row-3{top:1210px}.row-4{top:1772px}.row-5{top:2333px}
</style>
</head>
<body>
<svg width="0" height="0" style="position:absolute" aria-hidden="true">
  <defs>
    <linearGradient id="photoTone" x1="0" y1="0" x2="0.4" y2="1">
      <stop offset="0" stop-color="#d8c6b6"/>
      <stop offset="0.55" stop-color="#8a7376"/>
      <stop offset="1" stop-color="#3d3346"/>
    </linearGradient>
    <symbol id="hex" viewBox="-1 -1 2 2">
      <polygon points="0,-0.78 0.68,-0.39 0.68,0.39 0,0.78 -0.68,0.39 -0.68,-0.39" stroke-width="0.4" stroke-linejoin="round"/>
    </symbol>
  </defs>
</svg>

<main class="board">

  <!-- 1 -->
  <section class="post col-l row-1"><div class="post-art">
    <svg class="shapes" viewBox="0 0 375 469">
      <g role="img" aria-label="Photo of two smiling women standing side by side"><polygon class="photo" points="112,0 375,0 375,180 272,222 152,205 112,150"/></g>
      <polygon class="plum panel" points="-20,250 92,212 200,212 250,300 250,490 -20,490"/>
      <polygon class="plum panel" points="325,240 395,210 395,330 325,330"/>
      <use href="#hex" class="pink" x="5" y="28" width="76" height="76"/>
      <use href="#hex" class="pink" x="57" y="122" width="20" height="20"/>
      <use href="#hex" class="pink" x="278" y="390" width="52" height="52"/>
      <use href="#hex" class="pink" x="325" y="366" width="18" height="18"/>
    </svg>
    <h2 class="headline" style="left:22px;top:255px"><span class="accent">Stop Starting</span><br>Over Every<br><em>Monday</em></h2>
    <p class="tagline" style="left:20px;top:382px"><span class="accent">Stay Consistent with</span><br>RT in Your Pocket!</p>
  </div></section>

  <!-- 2 -->
  <section class="post col-r row-1"><div class="post-art">
    <svg class="shapes" viewBox="0 0 375 469">
      <polygon class="plum panel" points="-20,-20 252,-20 252,160 170,270 -20,270"/>
      <g role="img" aria-label="Photo of a smiling woman in a black lace top"><polygon class="photo" points="145,200 225,168 395,200 395,490 210,490 145,410"/></g>
      <use href="#hex" class="plum" x="297" y="28" width="46" height="46"/>
      <use href="#hex" class="pink" x="339" y="88" width="20" height="20"/>
      <use href="#hex" class="pink" x="38" y="342" width="64" height="64"/>
      <use href="#hex" class="pink" x="22" y="300" width="20" height="20"/>
      <circle class="plum" cx="139" cy="442" r="4"/>
    </svg>
    <h2 class="headline" style="left:24px;top:18px;font-size:30px;line-height:1.15">You don't need<br>more willpower.<br><em>You need more<br>support</em></h2>
    <p class="tagline" style="left:22px;top:166px"><span class="accent">Stay Consistent<br>with</span> RT in Your<br>Pocket!</p>
  </div></section>

  <!-- 3 -->
  <section class="post col-l row-2"><div class="post-art">
    <svg class="shapes" viewBox="0 0 375 469">
      <g role="img" aria-label="Photo of two women hugging and laughing"><polygon class="photo" points="150,40 200,5 395,-10 395,268 300,268 150,195"/></g>
      <polygon class="plum panel" points="-20,120 130,120 270,260 205,420 -20,420"/>
      <use href="#hex" class="pink" x="106" y="22" width="50" height="50"/>
      <use href="#hex" class="pink" x="17" y="72" width="20" height="20"/>
      <use href="#hex" class="pink" x="305" y="305" width="50" height="50"/>
      <use href="#hex" class="pink" x="276" y="368" width="18" height="18"/>
    </svg>
    <h2 class="headline" style="left:22px;top:133px;line-height:1.2">Built<br>for<br>women<br>who are tired<br>of doing this<br>alone</h2>
    <p class="tagline" style="left:20px;top:370px"><span class="accent">Stay Consistent with</span><br>RT in Your Pocket!</p>
  </div></section>

  <!-- 4 -->
  <section class="post col-r row-2"><div class="post-art">
    <svg class="shapes" viewBox="0 0 375 469">
      <g role="img" aria-label="Photo of a smiling woman in a black lace top, hand on hip"><polygon class="photo" points="62,-10 312,-10 312,140 245,192 135,192 62,140"/></g>
      <polygon class="plum panel" points="38,490 38,290 128,228 245,228 337,290 337,490"/>
      <use href="#hex" class="plum" x="12" y="96" width="66" height="66"/>
      <use href="#hex" class="pink" x="310" y="170" width="58" height="58"/>
      <use href="#hex" class="pink" x="340" y="130" width="20" height="20"/>
      <circle class="plum" cx="23" cy="228" r="4"/>
    </svg>
    <h2 class="headline center" style="top:246px;font-size:33px;line-height:1.25">When<br>Motivation Fades,<br><em>RT Checks In</em></h2>
    <p class="tagline center" style="top:391px"><span class="accent">Stay Consistent</span><br><span class="accent">with</span> RT in Your Pocket!</p>
  </div></section>

  <!-- 5 -->
  <section class="post col-l row-3"><div class="post-art">
    <svg class="shapes" viewBox="0 0 375 469">
      <polygon class="plum panel" points="185,-20 395,-20 395,290 250,290 118,160"/>
      <g role="img" aria-label="Photo of two smiling women standing side by side"><polygon class="photo" points="-20,205 100,200 218,265 218,490 -20,490"/></g>
      <use href="#hex" class="pink" x="8" y="62" width="58" height="58"/>
      <use href="#hex" class="pink" x="88" y="57" width="22" height="22"/>
      <use href="#hex" class="pink" x="310" y="262" width="74" height="74"/>
      <use href="#hex" class="plum" x="268" y="350" width="30" height="30"/>
      <use href="#hex" class="pink" x="305" y="430" width="16" height="16"/>
    </svg>
    <h2 class="headline" style="left:150px;top:50px;line-height:1.2">The Support<br>System You've<br>Been Missing</h2>
    <p class="tagline" style="left:221px;top:185px;font-size:15px"><span class="accent">Stay Consistent<br>with</span> RT in Your<br>Pocket!</p>
  </div></section>

  <!-- 6 -->
  <section class="post col-r row-3"><div class="post-art">
    <svg class="shapes" viewBox="0 0 375 469">
      <g role="img" aria-label="Photo of two women hugging and laughing"><polygon class="photo" points="-20,-20 262,-20 262,170 188,222 60,205 -20,170"/></g>
      <polygon class="plum panel" points="-20,200 30,225 30,340 -20,365"/>
      <polygon class="plum panel" points="105,490 105,300 208,215 305,215 395,270 395,490"/>
      <use href="#hex" class="pink" x="268" y="28" width="76" height="76"/>
      <use href="#hex" class="pink" x="275" y="122" width="20" height="20"/>
      <use href="#hex" class="pink" x="24" y="392" width="50" height="50"/>
      <use href="#hex" class="pink" x="9" y="366" width="20" height="20"/>
    </svg>
    <h2 class="headline" style="left:120px;top:278px;font-size:28px;line-height:1.18">Support When<br><span style="font-size:36px">Motivation</span><br>Disappears</h2>
    <p class="tagline" style="left:119px;top:402px"><span class="accent">Stay Consistent with</span><br>RT in Your Pocket!</p>
  </div></section>

  <!-- 7 -->
  <section class="post col-l row-4"><div class="post-art">
    <svg class="shapes" viewBox="0 0 375 469">
      <polygon class="plum panel" points="-20,40 62,62 62,250 -20,290"/>
      <g role="img" aria-label="Photo of a smiling woman in a black lace top"><polygon class="photo" points="158,60 215,12 395,-10 395,222 290,272 158,225"/></g>
      <polygon class="plum panel" points="-20,490 -20,340 105,252 230,262 268,330 268,490"/>
      <use href="#hex" class="pink" x="31" y="62" width="64" height="64"/>
      <use href="#hex" class="pink" x="100" y="200" width="20" height="20"/>
      <use href="#hex" class="pink" x="350" y="360" width="20" height="20"/>
      <use href="#hex" class="plum" x="308" y="376" width="48" height="48"/>
      <circle class="plum" cx="131" cy="24" r="4"/>
    </svg>
    <h2 class="headline" style="left:50px;top:272px;line-height:1.22">What if RT<br>Checked in<br>Every Day?</h2>
    <p class="tagline" style="left:48px;top:400px"><span class="accent">Stay Consistent with</span><br>RT in Your Pocket!</p>
  </div></section>

  <!-- 8 -->
  <section class="post col-r row-4"><div class="post-art">
    <svg class="shapes" viewBox="0 0 375 469">
      <polygon class="plum panel" points="38,-20 337,-20 337,160 250,220 125,220 38,160"/>
      <g role="img" aria-label="Photo of two smiling women standing side by side"><polygon class="photo" points="65,490 65,305 130,250 252,250 310,305 310,490"/></g>
      <use href="#hex" class="pink" x="10" y="232" width="56" height="56"/>
      <use href="#hex" class="pink" x="15" y="320" width="20" height="20"/>
      <use href="#hex" class="plum" x="296" y="300" width="70" height="70"/>
      <circle class="plum" cx="352" cy="235" r="4"/>
    </svg>
    <h2 class="headline center" style="top:20px;font-size:32px;line-height:1.32">The<br>Missing Piece<br>Isn't Another Diet</h2>
    <p class="tagline center" style="top:168px"><span class="accent">Stay Consistent</span><br><span class="accent">with</span> RT in Your Pocket!</p>
  </div></section>

  <!-- 9 -->
  <section class="post col-l row-5"><div class="post-art">
    <svg class="shapes" viewBox="0 0 375 469">
      <polygon class="plum panel" points="135,-20 395,-20 395,250 265,312 135,240"/>
      <g role="img" aria-label="Photo of two women hugging and laughing"><polygon class="photo" points="-20,225 92,195 242,262 242,490 -20,490"/></g>
      <use href="#hex" class="plum" x="44" y="28" width="48" height="48"/>
      <use href="#hex" class="pink" x="30" y="92" width="20" height="20"/>
      <use href="#hex" class="pink" x="288" y="342" width="66" height="66"/>
      <use href="#hex" class="pink" x="346" y="316" width="18" height="18"/>
    </svg>
    <h2 class="headline" style="left:145px;top:28px;font-size:28px;line-height:1.22"><em>Eat the food<br>you love.</em><br>Stay accountable<br>every day.</h2>
    <p class="tagline" style="left:221px;top:164px;font-size:15px"><span class="accent">Stay Consistent<br>with</span> RT in Your<br>Pocket!</p>
  </div></section>

  <!-- 10 -->
  <section class="post col-r row-5"><div class="post-art">
    <svg class="shapes" viewBox="0 0 375 469">
      <g role="img" aria-label="Photo of a smiling woman in a black lace top, hand on hip"><polygon class="photo" points="-20,25 100,25 175,115 175,290 -20,290"/></g>
      <polygon class="plum panel" points="160,-20 275,-20 275,60 235,102 178,95 160,40"/>
      <polygon class="plum panel" points="172,490 172,300 228,158 395,158 395,490"/>
      <use href="#hex" class="pink" x="318" y="76" width="50" height="50"/>
      <use href="#hex" class="pink" x="318" y="62" width="0" height="0"/>
      <use href="#hex" class="pink" x="349" y="5" width="20" height="20"/>
      <use href="#hex" class="pink" x="326" y="56" width="18" height="18"/>
      <use href="#hex" class="pink" x="36" y="344" width="72" height="72"/>
      <use href="#hex" class="pink" x="86" y="440" width="20" height="20"/>
      <circle class="plum" cx="131" cy="380" r="4"/>
    </svg>
    <h2 class="headline" style="left:223px;top:166px;font-size:28px;line-height:1.2"><span class="accent">One<br>Bad Meal</span><br>Doesn't<br>Mean You<br>Failed</h2>
    <p class="tagline" style="left:222px;top:346px;font-size:15px"><span class="accent">Stay Consistent</span><br><span class="accent">with</span> RT in Your<br>Pocket!</p>
  </div></section>

</main>
</body>
</html>
```